Dentistry Office

We want a new design for a Dentist's office website.

The theme is: "We provide high quality, state-of-the-art, dental care in a comfortable, caring environment."

The site currently has a menu on the left of the page with about 40 items on it. There is a great deal of textual content on each page, plus several illustrations.

We want to do this using CSS, so we need specifications in the CSS for all possible elements. The CSS needs to be named in a logical manner for easy use.

Every dentist on the planet seems to use lots of Flash. We don't want to because it is so distracting. We are looking for an elegant solution targeting 24-55 age group, but not excluding anyone.

The following (from another dentist's site) can give you a taste of what we want to communicate on the site:

"After 20 years of teaching dentists how to refine their technique and many years of writing textbooks, I currently devote my time to my office and the hands-on practice of dentistry. I'd like to welcome you personally to my dental practice, and I invite you to meet my highly experienced team of professionals.

"We have offered complete dental care of the highest quality since 1978. We provide Preventive Services, Tooth Whitening and Cosmetic Dentistry for a beautiful smile, Endodontics (root canal treatment) to treat painful teeth, Sedation Dentistry so you can relax, and Dental Implants to restore what is missing. We offer total care.

"Our approach to your health is simple: We use our education, experience and dedication to provide every patient with superior dental care.

"This passion for excellence is not just a goal, but a standard every member of our team holds.

"We also pride ourselves with our state of the art procedures, training and technology. This includes creating a beautiful smile using techniques that preserve as much of the original tooth as possible.

"Our abilities are renowned throughout the dental profession and I hope if you have any questions you will contact us by an e-mail note, by phone or just by dropping by."

Keep in mind the screen shape and dimensions. Your design needs to work in the normal screen proportions, regardless of how it looks when you post it here. Scrolling is OK, but the first impression needs to work.
Updates

Keep in mind that there will be about 250 words, or more, on each page.

Competitors web sites:

http://www.brindlecovedentist.example/

http://www.brindlecovedentalcare.example/

http://www.grinsbymarlowvaledental.example/

http://www.tenbyfamilydentalcare.example/

http://www.quelmardental.example/

http://www.dovrinadental.example/

We need to compete with these.

Target Market(s)

Generally adults seeking the most experienced and comfortable-to-be-with dentist.

Industry/Entity Type

Training

Requirements
Must have
• Must stand apart from other dentists.
• Must be elegant.
• Must have a horizontal menu structure across all columns, NOT a vertical that requires scrolling, no popout, pop down, etc. menus.
• We are looking for something special.
• Do not waste your time or ours putting up templates and things you have used before.
• Personally, I do not see how someone outside the US can understand the northern California dental market. But you are welcome to try.
Should not have
• Flash or graphics that move
• The look of a template
• Folksy fonts
• Looks like you used it 20 times before

```html
<!DOCTYPE html>
<html lang="en">
<head>
<meta charset="utf-8">
<title>Dental Care – Welcome</title>
<link href="https://fonts.googleapis.com/css2?family=Cabin:wght@400;500&family=Vollkorn:wght@400&family=Parisienne&display=swap" rel="stylesheet">
<style>
  :root {
    --sky-top: #1d5f78;
    --sky-mid: #3f98b4;
    --sky-low: #a9dbe8;
    --nav-dark: #0b3a47;
    --nav-text: #d9eef3;
    --menu-blue: #86cfe0;
    --menu-line: #2e8ea7;
    --menu-text: #0e3a46;
    --ink: #111;
    --teal-head: #1c5d72;
    --frame: #ffffff;
    --foot-dark: #06323f;
  }
  * { box-sizing: border-box; margin: 0; padding: 0; }
  html, body { width: 1005px; height: 1200px; overflow: hidden; }
  body {
    position: relative;
    font-family: Arial, Helvetica, sans-serif;
    background: linear-gradient(180deg, #8fd0e1 336px, #cfeaf2 520px, #f4fafc 760px, #ffffff 900px);
  }
  .site-header {
    position: absolute; left: 0; top: 0; width: 1005px; height: 294px;
    background: linear-gradient(180deg, var(--sky-top) 0%, #2a7893 40%, var(--sky-mid) 70%, var(--sky-low) 100%);
    overflow: hidden;
  }
  .brand { position: absolute; left: 48px; top: 30px; }
  .brand-name { font-family: "Vollkorn", serif; font-size: 44px; color: #fff; line-height: 1; }
  .brand-tag { font-family: Arial, sans-serif; font-size: 11px; font-weight: bold; color: #0b1f26; margin-top: 4px; }
  .header-slogan {
    position: absolute; left: 32px; top: 160px; width: 310px;
    font-family: "Parisienne", cursive; font-size: 19.5px; line-height: 29px; color: #0d2a33;
  }
  .photo { position: absolute; background: var(--frame); padding: 8px; box-shadow: 0 2px 6px rgba(0,0,0,.3); }
  .photo .fill { width: 100%; height: 100%; }
  .photo-left { left: 345px; top: 95px; width: 150px; height: 230px; transform: rotate(-8deg); }
  .photo-left .fill { background: linear-gradient(135deg, #e7ecee, #b9c6cc 60%, #8a9aa2); }
  .photo-right { left: 830px; top: 80px; width: 140px; height: 240px; transform: rotate(6deg); }
  .photo-right .fill { background: linear-gradient(160deg, #f3f5f6, #d9c4b8 70%, #c8a895); }
  .photo-main { left: 458px; top: 35px; width: 400px; height: 270px; padding: 7px; }
  .photo-main .fill { background: linear-gradient(120deg, #eef2f3 0%, #a9c7dc 40%, #e8d9b0 75%, #f1e6c8 100%); }

  .main-nav {
    position: absolute; left: 0; top: 294px; width: 1005px; height: 42px;
    background: var(--nav-dark);
    display: flex; align-items: center; padding-left: 20px;
    font-family: "Cabin", sans-serif; font-size: 17px; color: var(--nav-text);
  }
  .main-nav a { color: var(--nav-text); text-decoration: none; }
  .main-nav .sep { margin: 0 13.5px; }

  .side-menu {
    position: absolute; left: 15px; top: 352px; width: 225px; height: 713px;
    background: var(--menu-blue); border-radius: 7px; overflow: hidden;
  }
  .side-menu-title {
    height: 35px; background: linear-gradient(180deg, #2a2a2a, #0c0c0c);
    color: #f1f1f1; font-family: "Cabin", sans-serif; font-size: 16px;
    padding: 7px 0 0 23px;
  }
  .side-menu ul { list-style: none; margin-top: 17px; }
  .side-menu li {
    height: 30px; border-bottom: 1px dashed var(--menu-line);
    font-size: 12px; color: var(--menu-text); padding: 8px 0 0 20px;
    display: flex; align-items: flex-start; gap: 6px;
  }
  .side-menu li svg { margin-top: 2px; }

  .content { position: absolute; left: 276px; top: 352px; width: 707px; }
  .page-title {
    font-family: "Vollkorn", serif; font-weight: 400; color: var(--ink);
    font-size: 29px; padding: 8px 0 4px 4px; height: 59px;
    border-bottom: 1px dashed #5f8f9e;
  }
  .page-title span { color: var(--teal-head); font-size: 38px; }
  .intro-photo {
    position: absolute; left: 394px; top: 78px; width: 313px; height: 208px;
    background: #fff; padding: 8px; box-shadow: 0 1px 5px rgba(0,0,0,.25);
  }
  .intro-photo .fill { width: 100%; height: 100%; background: linear-gradient(110deg, #dbe3e6, #a7b4ba 45%, #e6e6e6 70%, #8c5a46); }
  .body-copy { font-size: 12px; line-height: 18px; color: var(--ink); padding: 25px 0 0 6px; width: 700px; }
  .body-copy p { margin-bottom: 18px; }
  .body-copy .narrow { width: 372px; }
  .body-copy .wide { width: 690px; }
  .body-copy .narrow + .wide { margin-top: 23px; }

  .feature-row { position: absolute; left: 283px; top: 897px; display: flex; gap: 27px; }
  .feature h2 { font-family: "Vollkorn", serif; font-weight: 400; font-size: 20px; color: var(--ink); margin: 0 0 15px 3px; }
  .feature .card {
    width: 215px; height: 126px; background: #fff; border: 1px solid #b9c4c8;
    border-radius: 7px; padding: 4px; box-shadow: 0 1px 3px rgba(0,0,0,.15);
  }
  .feature .fill { position: relative; width: 100%; height: 100%; border-radius: 3px; }
  .card-call .fill { background: linear-gradient(90deg, #dfe8ee, #c7d6de 50%, #b46a4c); }
  .card-implants .fill { background: linear-gradient(100deg, #e9ecee, #cfd6da 55%, #e0b9a3); }
  .card-team .fill { background: linear-gradient(90deg, #eef3f5, #d8e2e6 50%, #c6d4de); }
  .card-label {
    position: absolute; left: 10px; bottom: 10px;
    font-family: "Vollkorn", serif; color: #fff; font-size: 19px;
    font-variant-numeric: lining-nums;
    text-shadow: 0 0 3px #0b3a47, 0 0 2px #0b3a47;
    display: flex; align-items: center; gap: 6px;
    white-space: nowrap;
  }
  .card-call .card-label { font-size: 29px; bottom: 16px; }

  .site-footer {
    position: absolute; left: 0; top: 1100px; width: 1005px; height: 100px;
    background: var(--foot-dark);
  }
  .site-footer svg.edge { position: absolute; left: 0; top: -1px; }
  .footer-links {
    position: absolute; right: 24px; top: 40px; font-size: 11px; color: #fff; white-space: nowrap;
  }
  .footer-links .sep { margin: 0 9.5px; }
</style>
</head>
<body>
  <header class="site-header">
    <div class="brand">
      <div class="brand-name">Dental Care</div>
      <div class="brand-tag">The Best Dental Care of Northern California</div>
    </div>
    <p class="header-slogan">We provide high quality, state-of-the-art, dental care in a comfortable, caring environment.</p>
    <div class="photo photo-left"><div class="fill" role="img" aria-label="Photo of a dentist in a mask treating a patient"></div></div>
    <div class="photo photo-right"><div class="fill" role="img" aria-label="Photo of a relaxed patient in the dental chair"></div></div>
    <div class="photo photo-main"><div class="fill" role="img" aria-label="Photo of a smiling hygienist showing dental floss to a patient"></div></div>
  </header>

  <nav class="main-nav">
    <a href="#">Home</a><span class="sep">|</span>
    <a href="#">About Us</a><span class="sep">|</span>
    <a href="#">Our Practice</a><span class="sep">|</span>
    <a href="#">Procedures</a><span class="sep">|</span>
    <a href="#">Our Mission</a><span class="sep">|</span>
    <a href="#">Dental Implants</a><span class="sep">|</span>
    <a href="#">FAQs</a><span class="sep">|</span>
    <a href="#">Smile Gallery</a><span class="sep">|</span>
    <a href="#">Contact US</a>
  </nav>

  <aside class="side-menu">
    <div class="side-menu-title">Left Menu</div>
    <ul>
      <li><svg width="12" height="10"><path d="M1 5h6M5 2l3 3-3 3" stroke="#0e3a46" fill="none"/><circle cx="10" cy="5" r="1" fill="#0e3a46"/></svg>Lorem Ipsum Dolor Sit Amet</li>
      <li><svg width="12" height="10"><path d="M1 5h6M5 2l3 3-3 3" stroke="#0e3a46" fill="none"/><circle cx="10" cy="5" r="1" fill="#0e3a46"/></svg>Lorem Ipsum Dolor Sit Amet</li>
      <li><svg width="12" height="10"><path d="M1 5h6M5 2l3 3-3 3" stroke="#0e3a46" fill="none"/><circle cx="10" cy="5" r="1" fill="#0e3a46"/></svg>Lorem Ipsum Dolor Sit Amet</li>
      <li><svg width="12" height="10"><path d="M1 5h6M5 2l3 3-3 3" stroke="#0e3a46" fill="none"/><circle cx="10" cy="5" r="1" fill="#0e3a46"/></svg>Lorem Ipsum Dolor Sit Amet</li>
      <li><svg width="12" height="10"><path d="M1 5h6M5 2l3 3-3 3" stroke="#0e3a46" fill="none"/><circle cx="10" cy="5" r="1" fill="#0e3a46"/></svg>Lorem Ipsum Dolor Sit Amet</li>
      <li><svg width="12" height="10"><path d="M1 5h6M5 2l3 3-3 3" stroke="#0e3a46" fill="none"/><circle cx="10" cy="5" r="1" fill="#0e3a46"/></svg>Lorem Ipsum Dolor Sit Amet</li>
      <li><svg width="12" height="10"><path d="M1 5h6M5 2l3 3-3 3" stroke="#0e3a46" fill="none"/><circle cx="10" cy="5" r="1" fill="#0e3a46"/></svg>Lorem Ipsum Dolor Sit Amet</li>
      <li><svg width="12" height="10"><path d="M1 5h6M5 2l3 3-3 3" stroke="#0e3a46" fill="none"/><circle cx="10" cy="5" r="1" fill="#0e3a46"/></svg>Lorem Ipsum Dolor Sit Amet</li>
      <li><svg width="12" height="10"><path d="M1 5h6M5 2l3 3-3 3" stroke="#0e3a46" fill="none"/><circle cx="10" cy="5" r="1" fill="#0e3a46"/></svg>Lorem Ipsum Dolor Sit Amet</li>
      <li><svg width="12" height="10"><path d="M1 5h6M5 2l3 3-3 3" stroke="#0e3a46" fill="none"/><circle cx="10" cy="5" r="1" fill="#0e3a46"/></svg>Lorem Ipsum Dolor Sit Amet</li>
      <li><svg width="12" height="10"><path d="M1 5h6M5 2l3 3-3 3" stroke="#0e3a46" fill="none"/><circle cx="10" cy="5" r="1" fill="#0e3a46"/></svg>Lorem Ipsum Dolor Sit Amet</li>
      <li><svg width="12" height="10"><path d="M1 5h6M5 2l3 3-3 3" stroke="#0e3a46" fill="none"/><circle cx="10" cy="5" r="1" fill="#0e3a46"/></svg>Lorem Ipsum Dolor Sit Amet</li>
      <li><svg width="12" height="10"><path d="M1 5h6M5 2l3 3-3 3" stroke="#0e3a46" fill="none"/><circle cx="10" cy="5" r="1" fill="#0e3a46"/></svg>Lorem Ipsum Dolor Sit Amet</li>
      <li><svg width="12" height="10"><path d="M1 5h6M5 2l3 3-3 3" stroke="#0e3a46" fill="none"/><circle cx="10" cy="5" r="1" fill="#0e3a46"/></svg>Lorem Ipsum Dolor Sit Amet</li>
      <li><svg width="12" height="10"><path d="M1 5h6M5 2l3 3-3 3" stroke="#0e3a46" fill="none"/><circle cx="10" cy="5" r="1" fill="#0e3a46"/></svg>Lorem Ipsum Dolor Sit Amet</li>
      <li><svg width="12" height="10"><path d="M1 5h6M5 2l3 3-3 3" stroke="#0e3a46" fill="none"/><circle cx="10" cy="5" r="1" fill="#0e3a46"/></svg>Lorem Ipsum Dolor Sit Amet</li>
      <li><svg width="12" height="10"><path d="M1 5h6M5 2l3 3-3 3" stroke="#0e3a46" fill="none"/><circle cx="10" cy="5" r="1" fill="#0e3a46"/></svg>Lorem Ipsum Dolor Sit Amet</li>
      <li><svg width="12" height="10"><path d="M1 5h6M5 2l3 3-3 3" stroke="#0e3a46" fill="none"/><circle cx="10" cy="5" r="1" fill="#0e3a46"/></svg>Lorem Ipsum Dolor Sit Amet</li>
      <li><svg width="12" height="10"><path d="M1 5h6M5 2l3 3-3 3" stroke="#0e3a46" fill="none"/><circle cx="10" cy="5" r="1" fill="#0e3a46"/></svg>Lorem Ipsum Dolor Sit Amet</li>
      <li><svg width="12" height="10"><path d="M1 5h6M5 2l3 3-3 3" stroke="#0e3a46" fill="none"/><circle cx="10" cy="5" r="1" fill="#0e3a46"/></svg>Lorem Ipsum Dolor Sit Amet</li>
      <li><svg width="12" height="10"><path d="M1 5h6M5 2l3 3-3 3" stroke="#0e3a46" fill="none"/><circle cx="10" cy="5" r="1" fill="#0e3a46"/></svg>Lorem Ipsum Dolor Sit Amet</li>
    </ul>
  </aside>

  <main class="content">
    <h1 class="page-title">welcome to <span>Dental Care</span></h1>
    <div class="intro-photo"><div class="fill" role="img" aria-label="Photo of a dentist talking with a patient in the treatment chair"></div></div>
    <div class="body-copy">
      <p class="narrow">"After 20 years of teaching dentists how to refine their technique and many years of writing textbooks, I currently devote my time to my office and the hands-on practice of dentistry. I'd like to welcome you personally to my dental practice, and I invite you to meet my highly experienced team of professionals.</p>
      <p class="narrow">"We have offered complete dental care of the highest quality since 1978. We provide Preventive Services, Tooth Whitening and Cosmetic Dentistry for a beautiful smile, Endodontics (root canal treatment) to treat painful teeth, Sedation Dentistry so you can relax, and Dental Implants to restore what is missing. We offer total care.</p>
      <p class="wide">"Our approach to your health is simple: We use our education, experience and dedication to provide every patient with superior dental care.</p>
      <p class="wide">"This passion for excellence is not just a goal, but a standard every member of our team holds.</p>
      <p class="wide">"We also pride ourselves with our state of the art procedures, training and technology. This includes creating a beautiful smile using techniques that preserve as much of the original tooth as possible.</p>
      <p class="wide">"Our abilities are renowned throughout the dental profession and I hope if you have any questions you will contact us by an e-mail note, by phone or just by dropping by."</p>
    </div>
  </main>

  <section class="feature-row">
    <div class="feature card-call">
      <h2>Call Us</h2>
      <div class="card"><div class="fill" role="img" aria-label="Photo of a woman talking on the phone"><span class="card-label">555..010.4826</span></div></div>
    </div>
    <div class="feature card-implants">
      <h2>Dental Implants</h2>
      <div class="card"><div class="fill" role="img" aria-label="Photo of a dentist showing a denture model to a patient"><span class="card-label">More Information
        <svg width="24" height="24" viewBox="0 0 24 24"><circle cx="12" cy="12" r="11" fill="#111" stroke="#fff" stroke-width="1.5"/><path d="M6 12h11M13 8l4 4-4 4" stroke="#fff" stroke-width="2" fill="none"/></svg></span></div></div>
    </div>
    <div class="feature card-team">
      <h2>Meet The Dentists</h2>
      <div class="card"><div class="fill" role="img" aria-label="Photo of two members of the dental team"><span class="card-label">View List of Dentists</span></div></div>
    </div>
  </section>

  <footer class="site-footer">
    <svg class="edge" width="1005" height="6" viewBox="0 0 1005 6">
      <defs><pattern id="scallop" width="8" height="6" patternUnits="userSpaceOnUse"><circle cx="4" cy="0" r="3" fill="#ffffff"/></pattern></defs>
      <rect width="1005" height="6" fill="url(#scallop)"/>
    </svg>
    <div class="footer-links">
      © Copyright Dental Care<span class="sep">|</span>All Rigghts &nbsp;Reserved &nbsp;&nbsp;Home<span class="sep">|</span>About Us<span class="sep">|</span>Our Practice<span class="sep">|</span>Procedures<span class="sep">|</span>Our Mission<span class="sep">|</span>Dental Implants<span class="sep">|</span>FAQs<span class="sep">|</span>Smile Gallery<span class="sep">|</span>Contact Us
    </div>
  </footer>
</body>
</html>
```